Marwick Law Letterhead

We need a new letterhead design for a Law Firm. The address for the law firm is 1475 Calloway Street, Suite 210, Houston, Texas 77041. Phone Number: 832-361-9027; Fax Number: 832-614-7359. The logo is uploaded to the project.

```html
<!DOCTYPE html>
<html lang="en">
<head>
<meta charset="utf-8">
<title>Marwick Law Letterhead</title>
<link rel="stylesheet" href="https://fonts.googleapis.com/css2?family=Montserrat:wght@400;500;600&family=Mrs+Saint+Delafield&display=swap">
<style>
  :root {
    --red: #c8182a;
    --red-deep: #7e0c18;
    --navy: #1f3470;
    --ink: #1e1e22;
    --paper: #ffffff;
    --backdrop: #e8e8ea;
  }
  * { margin: 0; padding: 0; box-sizing: border-box; }
  html, body { width: 1200px; height: 960px; overflow: hidden; background: var(--backdrop); }
  body { position: relative; font-family: "Montserrat", sans-serif; color: var(--ink); }

  .letterhead {
    position: absolute; left: 282px; top: 30px;
    width: 636px; height: 900px;
    background: var(--paper);
    box-shadow: 0 4px 18px rgba(0,0,0,0.12);
    overflow: hidden;
  }
  .swoosh { position: absolute; inset: 0; width: 100%; height: 100%; }

  .brand {
    position: absolute; left: 40px; top: 158px;
    display: flex; align-items: center; gap: 10px;
  }
  .brand-dot { width: 24px; height: 24px; border-radius: 50%; background: var(--red); }
  .brand-name { font-size: 21px; font-weight: 600; color: var(--navy); letter-spacing: 0.5px; }

  .contact {
    position: absolute; left: 430px; top: 118px;
    font-size: 9.5px; line-height: 13px; color: var(--ink); font-style: normal;
  }
  .contact .phone { display: flex; align-items: center; gap: 6px; margin-top: 2px; }
  .contact svg { width: 9px; height: 9px; fill: var(--red); }

  .recipient {
    position: absolute; left: 60px; top: 232px;
    font-size: 11px; line-height: 15px;
  }
  .body-copy {
    position: absolute; left: 80px; top: 300px; width: 500px;
    font-size: 10.5px; line-height: 15px;
  }
  .body-copy p { margin-bottom: 18px; }

  .closing { position: absolute; left: 80px; top: 712px; font-size: 11px; }
  .signature {
    font-family: "Mrs Saint Delafield", cursive;
    font-size: 30px; color: var(--ink); margin-top: 2px;
  }
</style>
</head>
<body>
  <main class="letterhead">
    <svg class="swoosh" viewBox="0 0 636 900" aria-hidden="true">
      <defs>
        <linearGradient id="redFade" x1="0" y1="0" x2="1" y2="1">
          <stop offset="0" stop-color="#c8182a"/>
          <stop offset="1" stop-color="#7e0c18"/>
        </linearGradient>
      </defs>
      <g class="header-wave">
        <path d="M0 0 H636 V10 C620 40 560 50 480 60 C330 80 150 80 60 110 C25 122 8 140 0 170 Z" fill="url(#redFade)"/>
        <path d="M636 26 C622 56 562 66 482 76 C332 96 152 96 62 126 C27 138 10 156 0 186" fill="none" stroke="#1f3470" stroke-width="5"/>
      </g>
      <g class="footer-wave" transform="rotate(180 318 450)">
        <path d="M0 0 H636 V10 C620 40 560 50 480 60 C330 80 150 80 60 110 C25 122 8 140 0 170 Z" fill="url(#redFade)"/>
        <path d="M636 26 C622 56 562 66 482 76 C332 96 152 96 62 126 C27 138 10 156 0 186" fill="none" stroke="#1f3470" stroke-width="5"/>
      </g>
    </svg>

    <div class="brand">
      <span class="brand-dot"></span>
      <span class="brand-name">Marwick Law</span>
    </div>

    <address class="contact">
      1475 Calloway Street,<br>
      Suite 210, Houston,<br>
      Texas 77041
      <div class="phone"><svg viewBox="0 0 24 24"><path d="M6.6 10.8a15 15 0 0 0 6.6 6.6l2.2-2.2c.3-.3.7-.4 1-.2 1.1.4 2.3.6 3.6.6.6 0 1 .4 1 1V20c0 .6-.4 1-1 1A17 17 0 0 1 3 4c0-.6.4-1 1-1h3.5c.6 0 1 .4 1 1 0 1.3.2 2.5.6 3.6.1.3 0 .7-.2 1z"/></svg>832-361-9027</div>
      <div class="phone"><svg viewBox="0 0 24 24"><path d="M6 3h10v5H6zM4 9h16a2 2 0 0 1 2 2v6h-4v4H6v-4H2v-6a2 2 0 0 1 2-2zm4 7v3h8v-3z"/></svg>832-614-7359</div>
    </address>

    <div class="recipient">
      Mr/s<br>
      First Name and Last Name<br>
      Company Name<br>
      Address
    </div>

    <section class="body-copy">
      <p>Lorem ipsum dolor sit amet,consectetur adipiscing sed do eiusmod tempor incididunt laboreet dolore magna aliqua.Ut enim ad minim,veniam, quis nostrud exercitation ullamco laboris nisi ut aliquip exea commodo consequat.Lorem ipsum dolor sit amet,consectetur adipiscing sed do eiusmod tempor incididunt.labore et dolore magna aliqua. Ut enim</p>
      <p>Lorem ipsum dolor sit amet, consectetur adipiscing sed do eiusmod tempor incididunt labore et dolore magna aliqua. Ut enim ad minim veniam, quis nostrud exercitation ullamco laboris nisi ut aliquip exea commodo consequat.Duis aute irure dolor in reprehenderit in voluptate velit esse cillum irure dolor in reprehenderit in voluptate velit esse irure</p>
      <p>Lorem ipsum dolor sit amet, consectetur adipiscing sed do eiusmod tempor incididunt labore et dolore magna aliqua. consequat. Duis aute irure dolor in.reprehenderit in voluptate velit esse cillum dolore eu fugiat nulla pariatur. Excepteur sint occaecat cupidatat non proident, sunt in culpa qui officia deserunt mollit,</p>
      <p>Lorem ipsum dolor sit amet, consectetur adipiscing sed do eiusmod tempor incididunt labore et dolore magna aliqua. Ut enim Lorem ipsum dolor sit amet, consectetur adipiscing sed do eiusmod tempor incididunt labore et dolore magna aliqua. Ut enim Lorem ipsum aliqua.ipsum</p>
      <p>Lorem ipsum dolor sit amet, consectetur adipiscing sed do eiusmod tempor incididunt labore et dolore magna aliqua. Ut enim ad minim veniam, quis nostrud exercitation ullamco laboris nisi ut aliquip exea commodo consequat.Duis aute irure dolor in reprehenderit in voluptate velit esse cillum irure dolor in reprehenderit in voluptate velit esse irure</p>
    </section>

    <div class="closing">
      Regards
      <div class="signature">Halvorsen</div>
    </div>
  </main>
</body>
</html>
```